Architectural, Engineering and Design Build

Tovandex4.com
Veteran Disabled Certified company is doing business in Architecture, Engineer and Design build - look simialr websites and come up with design follow following website
https://hollis-darnet.example/
https://www.venlorcogroup.example/
https://www.pembrisgc.example/contract-vehicles/service-disabled-veteran-owned-small-business-sdvosb/
https://www.corbelnetlink.example/about/sdvosb/

Target Market(s)

US - Defense and Federal Government

Industry/Entity Type

Colors
0054AA
0677BA
7BADD7
CADEEF
E8F1F8

Requirements
Must have
• Army, American patriotism , Buildings, construction, architecture, engineering
Nice to have
• I need to attract federal government agencies and Defense

```html
<!DOCTYPE html>
<html lang="en">
<head>
<meta charset="utf-8">
<title>Tovandex4 — Building for the Future of Defense</title>
<link href="https://fonts.googleapis.com/css2?family=Exo+2:wght@500;600;700&family=Nunito+Sans:wght@400;600;700&display=swap" rel="stylesheet">
<style>
:root{
  --navy:#141f6b;
  --red:#e3141b;
  --grey-bg:#f0f0f0;
  --text:#333842;
  --muted:#555b66;
  --white:#ffffff;
  --head:"Exo 2", sans-serif;
  --body:"Nunito Sans", sans-serif;
}
*{box-sizing:border-box;margin:0;padding:0}
html,body{width:1200px;height:4886px;overflow:hidden}
body{position:relative;font-family:var(--body);color:var(--text);background:var(--white)}
.abs{position:absolute}
.sec{position:absolute;left:0;width:1200px}
h1,h2,h3{font-family:var(--head);color:#111;font-weight:700}
.sec-title{font-size:31px;text-transform:uppercase;letter-spacing:.2px;white-space:nowrap}
.center{text-align:center;left:0;width:1200px}
.underline{position:absolute;height:4px;width:46px;background:var(--red);border-radius:2px}
.btn{position:absolute;display:flex;align-items:center;justify-content:center;border-radius:22px;font-size:12px;font-weight:600;color:var(--white);background:var(--navy);white-space:nowrap}
.btn.red{background:var(--red)}
.para{font-size:12px;line-height:23px;color:var(--muted)}

.hero{top:0;height:600px;background:linear-gradient(180deg,#5d6e84 0%,#8c96a3 35%,#b7b4ad 60%,#7d7a73 100%)}
.hero-shade{position:absolute;inset:0;background:linear-gradient(180deg,rgba(10,15,35,.55),rgba(10,15,35,.25) 60%,rgba(10,15,35,.35))}
.brand{position:absolute;display:flex;align-items:center;gap:8px;font-family:var(--head);font-weight:700;color:var(--white);white-space:nowrap}
.brand .dot{border-radius:50%;border:3px solid var(--white)}
.nav{position:absolute;top:54px;left:0;width:1200px;font-size:12px;color:var(--white)}
.nav span{position:absolute;white-space:nowrap}
.nav .active{color:var(--red)}
.hero-title{position:absolute;top:274px;left:0;width:1200px;text-align:center;font-size:44px;color:var(--white);text-transform:uppercase}

.about-photo{left:150px;top:698px;width:400px;height:400px;border-radius:50%;background:linear-gradient(180deg,#5f8fbd 0%,#a9b9c4 45%,#e2a04a 75%,#3a2a1f 100%)}

.card{position:absolute;background:var(--white);border-radius:14px;box-shadow:0 2px 10px rgba(0,0,0,.06)}
.card-img{position:absolute;left:15px;top:14px;right:15px;height:244px;border-radius:10px}
.card h3{position:absolute;left:0;width:100%;text-align:center;font-family:var(--body);font-size:15px}
.card p{position:absolute;left:30px;right:30px;text-align:center;font-size:11.5px;line-height:20px;color:var(--muted)}
.arrow-dot{position:absolute;width:30px;height:30px;border-radius:50%;background:var(--navy)}

.badge{position:absolute;top:1928px;width:135px;height:84px;background:var(--white);border-radius:6px;box-shadow:0 2px 12px rgba(0,0,0,.1)}
.badge i{position:absolute;left:40px;top:20px;width:55px;height:44px;border-radius:6px}

.gal-img{position:absolute;top:2318px;height:245px;border-radius:6px}
.gal-title{position:absolute;font-family:var(--body);font-size:15px;line-height:22px;font-weight:700;color:#111;width:440px}

.why-card{position:absolute;top:3040px;width:284px;height:202px;background:var(--white);box-shadow:0 2px 14px rgba(0,0,0,.08)}
.why-card h3{position:absolute;top:95px;width:100%;text-align:center;font-family:var(--body);font-size:14px;line-height:20px}
.why-card p{position:absolute;top:144px;left:24px;right:24px;text-align:center;font-size:11.5px;line-height:19px;color:var(--muted)}
.why-icon{position:absolute;top:-34px;left:50%;margin-left:-48px;width:96px;height:96px}

.testi{position:absolute;left:152px;width:408px;height:205px;background:var(--white);border-radius:4px}
.avatar{position:absolute;left:140px;width:93px;height:90px;background:linear-gradient(180deg,#9a9682,#5f5b49)}
.quote-box{position:absolute;width:44px;height:68px;background:var(--red)}
.t-name{position:absolute;left:248px;font-family:var(--body);font-weight:700;font-size:15px;color:#111}
.stars{position:absolute;left:248px;color:#f2b400;font-size:13px;letter-spacing:3px}
.t-text{position:absolute;left:190px;width:335px;font-size:11.5px;line-height:23px;color:var(--muted)}

.cta{left:140px;top:4018px;width:918px;height:357px;border-radius:24px;background:radial-gradient(circle at 30% 40%,#d6262b,#b61e22 55%,#c8232a)}

.footer h4{position:absolute;top:4580px;font-family:var(--body);font-size:15px;color:var(--white);font-weight:700}
.footer .uline{position:absolute;top:4606px;width:28px;height:3px;background:var(--red)}
.flink{position:absolute;left:140px;font-size:11.5px;color:var(--white)}
.finfo{position:absolute;font-size:11.5px;line-height:18px;color:var(--white);white-space:nowrap}
.social{position:absolute;left:645px;display:flex;align-items:center;gap:12px;font-size:11.5px;color:var(--white)}
.social i{width:24px;height:24px;border:1.5px solid var(--white);border-radius:50%}
</style>
</head>
<body>

<section class="sec hero">
  <div class="abs" style="inset:0" role="img" aria-label="Photograph of a domed federal capitol building with grand stairway and flag"></div>
  <div class="hero-shade"></div>
  <div class="brand" style="left:140px;top:44px;font-size:28px"><span class="dot" style="width:22px;height:22px"></span>Tovandex4</div>
  <nav class="nav">
    <span class="active" style="left:634px">Home</span>
    <span style="left:714px">About Us</span>
    <span style="left:812px">Services</span>
    <span style="left:906px">Projects</span>
    <span style="left:998px">Contact Us</span>
  </nav>
  <h1 class="hero-title">Building for the Future of Defense</h1>
  <div class="btn red" style="left:522px;top:346px;width:155px;height:40px">Contact Us Today!</div>
</section>

<section class="sec" style="top:600px;height:588px">
  <svg class="abs" style="left:140px;top:88px" width="420" height="420" viewBox="0 0 420 420">
    <path d="M210 8 A202 202 0 0 0 70 360" fill="none" stroke="var(--red)" stroke-width="8"/>
    <path d="M70 360 A202 202 0 0 0 412 210 A202 202 0 0 0 300 30" fill="none" stroke="var(--navy)" stroke-width="7"/>
  </svg>
</section>
<div class="abs about-photo" role="img" aria-label="Photograph of construction workers silhouetted on scaffolding at sunset"></div>
<h2 class="abs sec-title" style="left:647px;top:748px">About Tovandex4</h2>
<div class="abs" style="left:647px;top:788px;width:46px;height:4px;background:var(--red);border-radius:2px"></div>
<p class="abs para" style="left:647px;top:810px;width:410px">Lorem ipsum dolor sit amet, consectetur adipiscing elit, sed do eiusmod tempor incididunt ut labore et dolore magna aliqua. Ut enim ad minim veniam, quis nostrud exercitation ullamco laboris nisi ut aliquip ex ea commodo consequat. Duis aute irure dolor in reprehenderit in voluptate velit esse cillum dolore eu fugiat nulla pariatur.</p>
<p class="abs para" style="left:647px;top:930px;width:410px"><b style="color:#111">Our Mission</b> : Sed ut perspiciatis unde omnis iste natus error sit amet ex ea voluptatem accusantium doloremque laudantium.</p>
<div class="btn" style="left:647px;top:1000px;width:127px;height:40px">Read More</div>
<div class="abs" style="left:975px;top:1015px;width:118px;height:40px;background:#f1f1f1" role="img" aria-label="Faint light grey decorative texture"></div>

<section class="sec" style="top:1188px;height:620px;background:var(--grey-bg)"></section>
<h2 class="abs sec-title center" style="top:1266px">Our Services</h2>
<div class="underline" style="left:577px;top:1306px"></div>
<div class="card" style="left:142px;top:1340px;width:290px;height:366px">
  <div class="card-img" style="background:linear-gradient(135deg,#e7e3da,#bdb6a8 60%,#e8c23a)" role="img" aria-label="Photograph of hands drafting architectural plans with a magnifier and hard hat"></div>
  <h3 style="top:274px">Architectural</h3>
  <p style="top:298px">Lorem ipsum dolor sit amet, consectetur adipiscing elit.</p>
  <div class="arrow-dot" style="left:130px;top:349px"></div>
</div>
<div class="card" style="left:455px;top:1340px;width:290px;height:366px">
  <div class="card-img" style="background:linear-gradient(180deg,#cfd3d4,#8f9a86 55%,#c8d148)" role="img" aria-label="Photograph of an engineer in hard hat and safety vest reading plans on site"></div>
  <h3 style="top:274px">Engineering Work</h3>
  <p style="top:298px">Lorem ipsum dolor sit amet, consectetur adipiscing elit.</p>
  <div class="arrow-dot" style="left:130px;top:349px"></div>
</div>
<div class="card" style="left:768px;top:1340px;width:290px;height:366px">
  <div class="card-img" style="background:linear-gradient(135deg,#6a5a4a,#d9d5cc 45%,#6d7a4a)" role="img" aria-label="Photograph of a designer sketching building drawings at a desk"></div>
  <h3 style="top:274px">Design Build</h3>
  <p style="top:298px">Lorem ipsum dolor sit amet, consectetur adipiscing elit.</p>
  <div class="arrow-dot" style="left:130px;top:349px"></div>
</div>
<svg class="abs" style="left:0;top:0;pointer-events:none" width="1200" height="1800">
  <g fill="none" stroke="#fff" stroke-width="2" stroke-linecap="round">
    <path d="M284 1698 l5 5 -5 5"/><path d="M597 1698 l5 5 -5 5"/><path d="M910 1698 l5 5 -5 5"/>
  </g>
</svg>

<h2 class="abs sec-title" style="left:140px;top:1886px">Key Industry Certifications</h2>
<div class="underline" style="left:140px;top:1926px"></div>
<p class="abs para" style="left:140px;top:1934px;width:460px">Sed ut perspiciatis unde omnis iste natus error sit voluptatem accusantium amet doloremque laudantium, totam rem aperiam, eaque ipsa quae ab illo.</p>
<div class="btn" style="left:140px;top:2005px;width:128px;height:40px">Contact Us</div>
<div class="badge" style="left:618px"><i style="background:#2c6fa8"></i></div>
<div class="badge" style="left:770px"><i style="background:var(--red)"></i></div>
<div class="badge" style="left:923px"><i style="background:var(--navy)"></i></div>

<section class="sec" style="top:2130px;height:698px;background:var(--grey-bg)"></section>
<h2 class="abs sec-title center" style="top:2208px">Project Gallery</h2>
<div class="underline" style="left:577px;top:2248px"></div>
<p class="abs para center" style="top:2272px">Sed ut perspiciatis unde omnis iste natus error sit voluptatem accusantium doloremque laudantium, totam rem aperiam, eaque ipsa quae ab illo.</p>
<div class="gal-img" style="left:140px;width:442px;background:linear-gradient(160deg,#3a5e8f,#c9a24a 55%,#6b4a20)" role="img" aria-label="Photograph of a building under construction with tower crane at golden hour"></div>
<div class="gal-img" style="left:617px;width:441px;background:linear-gradient(180deg,#9fc1dc,#8d8a82 45%,#54524c)" role="img" aria-label="Photograph of a classical federal building facade with columns and flag"></div>
<div class="gal-title" style="left:140px;top:2578px">Lorem Ipsum Is Simply Dummy Text Of The Printing And Typesetting Industry.</div>
<div class="gal-title" style="left:617px;top:2578px">Lorem Ipsum Is Simply Dummy Text Of The Printing And Typesetting Industry.</div>
<p class="abs para" style="left:140px;top:2629px;width:442px">Sed ut perspiciatis unde omnis iste natus error sit voluptatem accusantium amet doloremque laudantium, totam rem aperiam, eaque ipsa quae ab illo.</p>
<p class="abs para" style="left:617px;top:2629px;width:442px">Sed ut perspiciatis unde omnis iste natus error sit voluptatem accusantium amet doloremque laudantium, totam rem aperiam, eaque ipsa quae ab illo.</p>
<div class="btn" style="left:512px;top:2702px;width:176px;height:40px">Explore More Projects</div>

<h2 class="abs sec-title center" style="top:2904px">Why Choose Us</h2>
<div class="underline" style="left:577px;top:2944px"></div>
<p class="abs para center" style="top:2967px">Lorem ipsum dolor sit amet, consectetur adipiscing elit, sed do eiusmod tempor incididunt ut labore et dolore magna aliqua.</p>

<div class="why-card" style="left:140px">
  <svg class="why-icon" viewBox="0 0 96 96"><path d="M12 70 A42 42 0 0 0 60 88" fill="none" stroke="var(--red)" stroke-width="2.5"/><circle cx="48" cy="46" r="36" fill="var(--navy)"/><g fill="none" stroke="#fff" stroke-width="2"><rect x="36" y="38" width="24" height="20"/><path d="M34 38 h28 M44 30 v8 M52 30 v8 M40 64 h16"/></g></svg>
  <h3>Veteran-Owned<br>Business</h3>
  <p>Duis aute irure dolor in reprehenderit in voluptate velit esse cillum dolore.</p>
</div>
<div class="why-card" style="left:458px">
  <svg class="why-icon" viewBox="0 0 96 96"><path d="M14 30 A42 42 0 0 0 30 84 M66 84 A42 42 0 0 0 82 30" fill="none" stroke="var(--red)" stroke-width="2.5"/><circle cx="48" cy="46" r="36" fill="var(--navy)"/><g fill="none" stroke="#fff" stroke-width="2"><circle cx="48" cy="40" r="7"/><path d="M36 62 q12 -16 24 0 M38 34 h20"/></g></svg>
  <h3>Experience and<br>Expertise</h3>
  <p>Duis aute irure dolor in reprehenderit in voluptate velit esse cillum dolore.</p>
</div>
<div class="why-card" style="left:776px">
  <svg class="why-icon" viewBox="0 0 96 96"><path d="M48 4 A42 42 0 0 1 88 40" fill="none" stroke="var(--red)" stroke-width="2.5"/><circle cx="48" cy="46" r="36" fill="var(--navy)"/><g fill="none" stroke="#fff" stroke-width="2"><circle cx="48" cy="42" r="11"/><path d="M41 52 l-4 14 6 -3 3 5 M55 52 l4 14 -6 -3 -3 5"/><path d="M48 36 l2 4 4 .5 -3 3 1 4 -4-2 -4 2 1-4 -3-3 4-.5z"/></g></svg>
  <h3>Commitment to<br>Quality</h3>
  <p>Duis aute irure dolor in reprehenderit in voluptate velit esse cillum dolore.</p>
</div>

<section class="sec" style="top:3330px;height:600px;background:var(--grey-bg)"></section>
<div class="testi" style="top:3410px"></div>
<div class="avatar" style="top:3400px" role="img" aria-label="Portrait photo of a client in military uniform"></div>
<div class="quote-box" style="left:486px;top:3412px"></div>
<div class="t-name" style="top:3436px">Jane Smith</div>
<div class="stars" style="top:3456px">★★★★★</div>
<p class="t-text" style="top:3508px">Lorem ipsum dolor sit amet, consectetur adipiscing elit, sed do eiusmod tempor incididunt ut labore et dolore magna aliqua. Ut enim ad minim veniam, quis nostrud exercitation ullamco laboris nisi ut.</p>

<div class="testi" style="top:3643px"></div>
<div class="avatar" style="top:3633px" role="img" aria-label="Portrait photo of a client in military uniform"></div>
<div class="quote-box" style="left:486px;top:3645px"></div>
<div class="t-name" style="top:3669px">Emily Johnson</div>
<div class="stars" style="top:3689px">★★★★★</div>
<p class="t-text" style="top:3741px">Lorem ipsum dolor sit amet, consectetur adipiscing elit, sed do eiusmod tempor incididunt ut labore et dolore magna aliqua. Ut enim ad minim veniam, quis nostrud exercitation ullamco laboris nisi ut.</p>
<svg class="abs" style="left:0;top:0;pointer-events:none" width="1200" height="3800">
  <g fill="#fff" font-family="Georgia, serif" font-size="44" font-weight="700"><text x="493" y="3470">”</text><text x="493" y="3703">”</text></g>
</svg>

<h2 class="abs" style="left:650px;top:3406px;font-size:30px;text-transform:uppercase;white-space:nowrap">What Are People Saying?</h2>
<div class="underline" style="left:650px;top:3446px"></div>
<p class="abs para" style="left:650px;top:3469px;width:420px">Lorem Ipsum is simply dummy text of the printing and typesetting industry. Lorem Ipsum has been the industry's standard.</p>
<div class="abs" style="left:650px;top:3630px;font-family:var(--head);font-weight:700;font-size:78px;color:rgba(20,31,107,.07);white-space:nowrap">Tovandex4</div>
<svg class="abs" style="left:650px;top:3817px" width="90" height="36" viewBox="0 0 90 36">
  <circle cx="19" cy="18" r="16" fill="none" stroke="#222" stroke-width="1.5"/>
  <path d="M26 18 h-13 m5 -5 -5 5 5 5" fill="none" stroke="#222" stroke-width="2"/>
  <circle cx="68" cy="18" r="17" fill="var(--navy)"/>
  <path d="M61 18 h13 m-5 -5 5 5 -5 5" fill="none" stroke="#fff" stroke-width="2"/>
</svg>

<div class="abs cta" role="img" aria-label="Red camouflage textured banner background"></div>
<h2 class="abs center" style="top:4088px;font-size:34px;line-height:43px;color:#fff;font-weight:600">Lorem Ipsum Dolor Sit Amet, Consectetur<br>Adipiscing Elit</h2>
<p class="abs center" style="top:4192px;font-size:12.5px;line-height:23px;color:#fff">Lorem Ipsum is simply dummy text printing and typesetting industry. Lorem Ipsum has been the<br>industry's standard du ever since the 1500s, when an unknown printer took</p>
<div class="btn" style="left:522px;top:4262px;width:155px;height:38px">Project Cosultation</div>

<footer class="footer">
  <svg class="abs" style="left:0;top:4440px" width="1200" height="446" viewBox="0 0 1200 446">
    <path d="M0 140 Q600 -70 1200 140 L1200 446 L0 446 Z" fill="var(--navy)"/>
    <path d="M0 130 Q600 -82 1200 130" fill="none" stroke="var(--red)" stroke-width="3"/>
  </svg>
  <h4 style="left:140px">Quick Links</h4><div class="uline" style="left:140px"></div>
  <div class="flink" style="top:4636px">›&nbsp; Home</div>
  <div class="flink" style="top:4664px">›&nbsp; About Us</div>
  <div class="flink" style="top:4692px">›&nbsp; Services</div>
  <div class="flink" style="top:4720px">›&nbsp; Projects</div>
  <div class="flink" style="top:4748px">›&nbsp; Contact Us</div>

  <h4 style="left:343px">Contact Details</h4><div class="uline" style="left:343px"></div>
  <svg class="abs" style="left:342px;top:4636px" width="14" height="130" viewBox="0 0 14 130">
    <path d="M7 1 a5 5 0 0 1 5 5 c0 4 -5 9 -5 9 s-5 -5 -5 -9 a5 5 0 0 1 5 -5z" fill="#fff"/>
    <path d="M2 51 q1 -3 3 -1 l2 2 -1 2 q2 3 4 4 l2 -1 2 2 q0 3 -3 2 q-7 -2 -9 -10z" fill="#fff"/>
    <rect x="1" y="100" width="12" height="9" fill="#fff"/><path d="M1 100 l6 5 6 -5" fill="none" stroke="var(--navy)" stroke-width="1.2"/>
  </svg>
  <div class="finfo" style="left:364px;top:4634px">48, Harlow Plaza, Avenue<br>Fernwick, State QR 580214</div>
  <div class="finfo" style="left:364px;top:4684px"><b>Phone</b><br>555-0148-362</div>
  <div class="finfo" style="left:364px;top:4734px"><b>Email</b><br>info@tovandex4.com</div>

  <h4 style="left:645px">Follow Us</h4><div class="uline" style="left:645px"></div>
  <div class="social" style="top:4638px"><i></i>Pagebook</div>
  <div class="social" style="top:4678px"><i></i>Chirper</div>
  <div class="social" style="top:4719px"><i></i>Viewtube</div>
  <div class="social" style="top:4760px"><i></i>Snapgram</div>

  <div class="brand" style="left:858px;top:4646px;font-size:32px"><span class="dot" style="width:26px;height:26px"></span>Tovandex4</div>

  <div class="abs center" style="top:4858px;font-size:11px;color:#fff">© 2024 Tovandex4. All Rights Reserved</div>
</footer>

</body>
</html>
```